Personal Injury Lawyer Billboard

I would like a design created featuring the image of the lawyer centered in the middle of the design.
To the left of the lawyer's image it should read "INJURED?"
To the right of the lawyer's image, it should read "CALL DEAN!"
Under Call Dean, include the phone number 318-555-0187.
At the bottom of the design include the lawyers information "Dean Marlowe Accident & Injury Lawyers"
PLEASE REMOVED THE BACKGROUND IMAGERY OF THE PHOTO SUBMITTED. Also, the colors for this design should match the colors shown in the logo (navy, white and relective soft gold). Please use those color combinations in ways that best stand out.

```html
<!DOCTYPE html>
<html lang="en">
<head>
<meta charset="utf-8">
<title>Dean Marlowe Accident &amp; Injury Lawyers – Billboard</title>
<link rel="stylesheet" href="https://fonts.googleapis.com/css2?family=Cinzel:wght@700&display=swap">
<style>
  :root {
    --navy: #0b1d45;
    --navy-deep: #071634;
    --gold: #c9a23e;
    --white: #ffffff;
    --suit: #17284f;
    --suit-light: #2a3c66;
  }
  * { margin: 0; padding: 0; box-sizing: border-box; }
  html, body {
    width: 1200px;
    height: 879px;
    overflow: hidden;
    background: var(--navy);
  }
  .billboard {
    position: relative;
    width: 1200px;
    height: 879px;
    background: var(--navy);
    font-family: "Cinzel", "Times New Roman", serif;
    font-weight: 700;
  }
  .headline {
    position: absolute;
    left: 40px;
    top: 380px;
    color: var(--gold);
    font-size: 80px;
    line-height: 1;
    letter-spacing: 1px;
  }
  .firm-name {
    position: absolute;
    left: 40px;
    top: 560px;
    color: var(--white);
    line-height: 1.15;
  }
  .firm-name__primary {
    display: block;
    font-size: 44px;
    letter-spacing: 0.5px;
  }
  .firm-name__secondary {
    display: block;
    font-size: 20px;
    letter-spacing: 0.5px;
    margin-top: 8px;
  }
  .lawyer-portrait {
    position: absolute;
    left: 450px;
    top: 230px;
    width: 330px;
    height: 649px;
    border-radius: 150px 150px 0 0;
    background: linear-gradient(180deg, var(--suit-light) 0%, var(--suit) 45%, var(--navy-deep) 100%);
  }
  .call-to-action {
    position: absolute;
    left: 810px;
    top: 300px;
    width: 360px;
    text-align: center;
    color: var(--gold);
  }
  .call-to-action__label {
    font-size: 48px;
    line-height: 1;
    letter-spacing: 1px;
  }
  .call-to-action__icon {
    display: block;
    margin: 30px auto 28px;
    width: 72px;
    height: 72px;
  }
  .call-to-action__phone {
    font-size: 44px;
    line-height: 1;
    letter-spacing: 1px;
  }
</style>
</head>
<body>
  <main class="billboard">
    <h1 class="headline">INJURED</h1>

    <p class="firm-name">
      <span class="firm-name__primary">DEAN MARLOWE</span>
      <span class="firm-name__secondary">ACCIDENT &amp; INJURY LAWYERS</span>
    </p>

    <div class="lawyer-portrait" role="img" aria-label="Portrait of the lawyer in a navy suit and green tie, raising a fist"></div>

    <section class="call-to-action">
      <p class="call-to-action__label">CALL DEAN</p>
      <svg class="call-to-action__icon" viewBox="0 0 72 72" aria-hidden="true">
        <circle cx="36" cy="36" r="33" fill="none" stroke="var(--gold)" stroke-width="3"/>
        <path d="M24 20c2-1 4 0 5 2l3 6c1 2 0 3-1 4l-2 2c2 4 5 7 9 9l2-2c1-1 2-2 4-1l6 3c2 1 3 3 2 5l-2 3c-1 2-3 3-6 2-11-3-20-12-23-23-1-3 0-5 2-6z" fill="var(--gold)"/>
        <path d="M39 22a12 12 0 0 1 11 11" fill="none" stroke="var(--gold)" stroke-width="2.5" stroke-linecap="round"/>
        <path d="M39 15a19 19 0 0 1 18 18" fill="none" stroke="var(--gold)" stroke-width="2.5" stroke-linecap="round"/>
      </svg>
      <p class="call-to-action__phone">318-555-0187</p>
    </section>
  </main>
</body>
</html>
```